Brevard Trade Partners - we are Asian sourcing agents

We are sourcing agents based in the USA and we act as sourcing agents for clients in throughout the world. We focus primarily on custom sewn goods. So basically companies who do not have the in-house expertise to do it themselves, come to us and have us find suitable factories in Asia to do the production. We are middlemen. We find the factories...quote the project...manage the quality control and then deliver the goods directly to our customer's door. We pride ourselves in making the communication very easy and precise.

Current page is www.brevardtradepartners.com

I am not happy w/ the overall look. The spacing...the photos, the fonts...the design elements...the pictures. I want a cool, crisp design that conveys professionalism and clearly depicts/explains what we do.

Requirements
Must have
• use my logo....I like it...it was designed by someone on this website.
Nice to have
• a video/animation of the entire process would be wonderful. Showing initial contact with our office in the USA...then to my correspondence with my offices in Taiwan and in Hong Kong...and then back and fort w/ the customer.....and then between my people in Hong Kong/Taiwan with the local factories......and then a quote is generated and sent to my client......to samples being made and sent for approval.....to a PO being generated......to final samples being sent.....to the order being shipped and delivered to the clients warehouse. I was thinking of an animation showing arrows and text showing the back and forth communication and explaining how the process flows.

```html
<!DOCTYPE html>
<html lang="en">
<head>
<meta charset="utf-8">
<title>Brevard Trade Partners</title>
<link rel="stylesheet" href="https://fonts.googleapis.com/css2?family=Open+Sans:wdth,wght@75..100,400..800&display=swap">
<style>
:root{
  --green:#799418;
  --green-dark:#6b8414;
  --ink:#1f1f1f;
  --text:#4a4a4a;
  --paper:#f6f6f6;
  --panel:#ffffff;
  --dark:#1c1c1c;
  --dark-2:#222222;
  --white:#ffffff;
  --sky-1:#021a6e;
  --sky-2:#0b4fd8;
  --sky-3:#000a35;
}
*{box-sizing:border-box;margin:0;padding:0}
html,body{width:1200px;height:1166px;overflow:hidden}
body{font-family:"Open Sans",Arial,sans-serif;color:var(--text);position:relative}
.backdrop{position:absolute;inset:0;background:
  radial-gradient(ellipse at 12% 45%,var(--sky-2) 0%,transparent 45%),
  radial-gradient(ellipse at 88% 50%,var(--sky-2) 0%,transparent 45%),
  linear-gradient(180deg,var(--sky-1),var(--sky-3) 50%,var(--sky-1))}
.page{position:absolute;left:190px;top:0;width:820px;height:1166px}
.cond{font-stretch:75%;font-weight:700}

.masthead{display:flex;height:385px}
.sidebar{width:293px;background:var(--paper);padding:26px 0 0 34px}
.brand{display:flex;align-items:center;gap:10px;height:54px}
.brand-dot{width:50px;height:50px;border-radius:50%;background:var(--green)}
.brand-name{font-stretch:75%;font-weight:700;font-size:24px;line-height:1.05;color:var(--sky-1);width:170px}
.main-nav{list-style:none;margin:50px 0 0 7px}
.main-nav li{font-stretch:75%;font-weight:700;font-size:14px;color:var(--ink);height:28.7px;letter-spacing:.1px}
.hero{flex:1;background:radial-gradient(circle at 20% 45%,#9fd7ff 0%,#2c7ad0 20%,#123f8e 55%,#071e55 100%)}

.toolbar{height:62px;background:var(--green);display:flex;align-items:center;padding:0 0 0 25px}
.socials{display:flex;gap:6px}
.socials span{width:28px;height:28px;border-radius:50%;background:var(--white)}
.search{display:flex;margin-left:auto;height:31px}
.search-field{width:140px;background:var(--white);font-size:12px;color:#555;padding:8px 10px}
.search-btn{width:36px;border:1px solid var(--white);display:flex;align-items:center;justify-content:center}
.account{color:var(--white);font-size:12px;margin:0 22px 0 20px}

.intro{height:373px;background:var(--paper);display:flex;padding:38px 0 0 25px}
.intro-main{width:433px}
.intro-main h1{font-stretch:75%;font-weight:700;font-size:31px;color:var(--ink);margin:0 0 14px 3px;letter-spacing:.3px}
.intro-main p{font-size:12.2px;line-height:22px}
.benefits{margin-left:39px;width:300px;padding-top:0}
.benefit{margin-bottom:22px}
.benefit h2{font-stretch:75%;font-weight:700;font-size:19px;color:var(--green);margin-bottom:6px}
.benefit p{font-size:12.2px;line-height:17px}

.bottom{display:flex;height:265px}
.faq{width:332px;background:var(--green);padding:32px 0 0 25px;color:var(--white)}
.faq h3{font-stretch:75%;font-weight:700;font-size:26px;margin-bottom:12px}
.faq ul{list-style:none;padding-left:3px}
.faq li{font-size:13.5px;height:25.7px}
.contact-card{width:214px;background:var(--dark);border-left:1px solid #444;display:flex;flex-direction:column;align-items:center;padding-top:41px}
.portrait{width:106px;height:106px;border-radius:50%;border:3px solid #ddd;background:radial-gradient(circle at 50% 40%,#c9c3bd,#5d6470)}
.quote-btn{margin-top:24px;width:175px;height:51px;border:1.5px solid var(--white);color:var(--white);font-stretch:75%;font-weight:700;font-size:20px;display:flex;align-items:center;justify-content:center}
.pitch{flex:1;background:var(--dark-2);color:var(--white);padding:58px 10px 0 17px}
.pitch h3{font-stretch:75%;font-weight:700;font-size:19px;line-height:23.5px;margin-bottom:14px}
.pitch p{font-size:15.5px;line-height:17.5px}

.footer{height:81px;background:var(--paper);text-align:center;font-size:12.5px;line-height:18px;color:#333;padding-top:24px}
</style>
</head>
<body>
<div class="backdrop" role="img" aria-label="Blue glowing background of laptop keyboards and binary digits"></div>
<div class="page">
  <header class="masthead">
    <div class="sidebar">
      <div class="brand"><span class="brand-dot"></span><span class="brand-name">Brevard Trade Partners</span></div>
      <ul class="main-nav">
        <li>HOME</li><li>ABOUT US</li><li>PRODUCT CATEGORIES</li><li>SOURCING &amp; PROCURMENT</li><li>REQUEST QUOTE</li><li>CLIENTS</li><li>CONTACT US</li>
      </ul>
    </div>
    <div class="hero" role="img" aria-label="Photo of a hand touching a glowing world map interface titled Outsourcing"></div>
  </header>

  <div class="toolbar">
    <div class="socials"><span></span><span></span><span></span><span></span></div>
    <div class="search">
      <div class="search-field">Search Here...</div>
      <div class="search-btn"><svg width="16" height="16" viewBox="0 0 16 16"><circle cx="6.5" cy="6.5" r="5" fill="none" stroke="#fff" stroke-width="1.8"/><line x1="10.2" y1="10.2" x2="15" y2="15" stroke="#fff" stroke-width="2"/></svg></div>
    </div>
    <div class="account">Login / &nbsp;Register</div>
  </div>

  <section class="intro">
    <div class="intro-main">
      <h1>BREVARD TRADE PARTNERS</h1>
      <p>Lorem ipsum dolor sit amet, consectetur adipiscing elit. Praesent at tincidunt dolor, nec pulvinar elit. Vivamus imperdiet ipsum lacus, eu suscipit lacus maximus sed. Donec a posuere magna. Fusce finibus, elit nec semper convallis, odio magna feugiat nibh, eget feugiat elit nunc eu erat. Vestibulum ante ipsum primis in faucibus orci luctus et ultrices posuere cubilia Curae; Aliquam ac ipsum in mi luctus bibendum ac vitae nibh. Cras malesuada consequat dui, efficitur ultrices lectus aliquam ut. Nulla congue sollicitudin suscipit. Phasellus luctus fringilla diam convallis elementum. Curabitur quis lobortis est. Proin venenatis luctus efficitur. Nam tempor mattis nibh, id hendrerit felis malesuada ac. Aliquam sit amet urna eu nulla eleifend bibendum sed ut est. Mauris tempus sodales nibh, eget scelerisque sem viverra sed.</p>
    </div>
    <div class="benefits">
      <div class="benefit"><h2>ACCESS EMERGING MARKETS</h2><p>Lorem ipsum dolor sit amet, consectetur adipiscing elit. Praesent at tincidunt dolor, nec pulvinar elit. Vivamus imperdiet ipsum lacus, maximus sed.</p></div>
      <div class="benefit"><h2>REALISE VALUE BY SOURCING DIRECT</h2><p>Lorem ipsum dolor sit amet, consectetur adipiscing elit. Praesent at tincidunt dolor, nec pulvinar elit. Vivamus imperdiet ipsum lacus, maximus sed.</p></div>
      <div class="benefit"><h2>MANAGE QUALITY AND RELIABILITY RISKS</h2><p>Lorem ipsum dolor sit amet, consectetur adipiscing elit. Praesent at tincidunt dolor, nec pulvinar elit. Vivamus imperdiet ipsum lacus, maximus sed.</p></div>
    </div>
  </section>

  <section class="bottom">
    <div class="faq">
      <h3>WHAT DO YOU NEED TO KNOW</h3>
      <ul>
        <li>Contract Sewing in China</li><li>What is the Process?</li><li>What the Minimum Order?</li><li>Contract Outsourcing FAQ</li><li>Outsourcing Case Study</li><li>Custom Industrial Sewing in China</li>
      </ul>
    </div>
    <div class="contact-card">
      <div class="portrait" role="img" aria-label="Portrait photo of a smiling account manager"></div>
      <div class="quote-btn">REQUEST QUOTE</div>
    </div>
    <div class="pitch">
      <h3>OUTSOURCE YOUR SEWING NEEDS TO TRUSTED CONTRACTORS IN CHINA</h3>
      <p>Please contact us for immediate consultation regarding your outsourcing project.</p>
    </div>
  </section>

  <footer class="footer">
    © Copyright 2015, Brevard Trade Partners, LLC. All rights reserved.<br>
    Website Designed and Developed by Northlane Studio
  </footer>
</div>
</body>
</html>
```